New clean and fresh corporate PPT template for Telecom equipment maker

MPK (VORQEX MPKT) is a telecom equipment maker in Silicon Valley. Our current PPT template that goes with http://peltrovane.com is overbuilt, dark, huge in file size, and looks the opposite of fresh and clean.
Our new microsite @ http://investor-mpkt.com is the direction we want to go. We are B2B, selling to telecom operators, but still want something that looks clean and fresh and not stuffy, hence primarily white background with maximum whitespace in 16:9 format.
Style guidelines attached, exclusive use of approved colors required, the master should remain as simple as possible, and we want the file size to stay reasonable (i.e. less is better). Features we would like include:
- Lato font built-in to the template
- Text boxes with standard size fonts, that automatically get smaller with indention
- An interesting bullet style, nothing crazy, but with visual interest
- A pre-selected table format that is clean and allows for high-density tables with many rows & columns
- Whichever standard slides layouts in the master you think would help result in slides that are found in the current deck, without someone needing to build their own slide

```html
<!DOCTYPE html>
<html lang="en">
<head>
<meta charset="utf-8">
<title>Safe Harbor Statement</title>
<link href="https://fonts.googleapis.com/css2?family=Lato:wght@400;700&display=swap" rel="stylesheet">
<style>
  :root {
    --ink: #111111;
    --slate: #4a5a6e;
    --teal: #4cc9c6;
    --lime: #8ccc1c;
    --coral: #f2706b;
    --muted: #8a8a8a;
    --mark: #b9bcc0;
    --paper: #ffffff;
  }
  * { margin: 0; padding: 0; box-sizing: border-box; }
  html, body { width: 1200px; height: 675px; overflow: hidden; background: var(--paper); }
  .slide {
    position: relative;
    width: 1200px;
    height: 675px;
    background: var(--paper);
    font-family: "Lato", Arial, sans-serif;
    color: var(--ink);
  }
  .slide-title {
    position: absolute;
    top: 33px;
    left: 0;
    width: 1200px;
    text-align: center;
    font-size: 46px;
    line-height: 56px;
    font-weight: 700;
    color: var(--slate);
    letter-spacing: -0.3px;
  }
  .accent-bar {
    position: absolute;
    top: 101px;
    left: 537px;
    display: flex;
    height: 4px;
  }
  .accent-bar span { width: 42px; height: 4px; }
  .accent-bar .teal { background: var(--teal); }
  .accent-bar .lime { background: var(--lime); }
  .accent-bar .coral { background: var(--coral); }
  .statement {
    position: absolute;
    top: 132px;
    left: 39px;
    width: 1125px;
  }
  .statement p {
    font-size: 20.3px;
    line-height: 31.25px;
    text-align: justify;
    text-indent: 90px;
    margin-bottom: 9px;
  }
  .brand-name {
    position: absolute;
    left: 16px;
    top: 616px;
    font-size: 36px;
    line-height: 44px;
    font-weight: 700;
    color: var(--mark);
    letter-spacing: -0.5px;
  }
  .copyright {
    position: absolute;
    top: 642px;
    left: 0;
    width: 1160px;
    text-align: center;
    font-size: 16px;
    color: var(--muted);
  }
  .page-marker {
    position: absolute;
    top: 624px;
    left: 1126px;
    width: 74px;
    height: 4px;
    background: var(--teal);
  }
  .page-number {
    position: absolute;
    top: 633px;
    left: 1128px;
    font-size: 20px;
    color: var(--slate);
  }
</style>
</head>
<body>
<div class="slide">
  <h1 class="slide-title">Safe Harbor Statement</h1>
  <div class="accent-bar"><span class="teal"></span><span class="lime"></span><span class="coral"></span></div>

  <div class="statement">
    <p>This presentation contains forward-looking statements that are subject to the safe harbors created under the Securities Act of 1933 and the Securities Exchange Act of 1934.&nbsp; Words such as “anticipate,” “believe,” “continue,” “could,” “estimate,” “expect,” “goal,” “intend,” “may,” “plan,” “project,” “seek,” “should,” “target,” “will,” “would,” variations of such words, and similar expressions are intended to identify forward-looking statements. In addition, forward-looking statements include, among others, statements that refer to financial estimates; projections of revenue, margins, expenses or other financial items. Readers are cautioned that actual results could differ materially from those expressed in or contemplated by the forward-looking statements.</p>
    <p>Factors that could cause actual results to differ include, but are not limited to, commercial acceptance of the Company's products; intense competition in the communications equipment market; the Company's ability to execute on its strategy and operating plans; and economic conditions specific to the communications, networking, internet and related industries. In addition, please refer to the risk factors contained in the Company's SEC filings available at www.sec.gov, including without limitation, the Company's annual report on Form 10-K and quarterly reports on Forms 10-Q. Readers are cautioned not to place undue reliance on any forward-looking statements, which speak only as of the date on which they are made. The Company undertakes no obligation to update or revise any forward-looking statements for any reason.</p>
  </div>

  <div class="brand-name">MPK</div>

  <div class="copyright">© 2018 Marpeck Solutions – Proprietary and Confidential</div>
  <div class="page-marker"></div>
  <div class="page-number">2</div>
</div>
</body>
</html>
```